Marrowby Water Taxi and Transport Business Card

I need business cards for my new water taxi and freight transport business I have started here in Kodiak Alaska. Kodiak is a remote island in the middle of the gulf of Alaska. There are seven native villages around the island and Kodiak is the #2 fishing port in the United States. We also have the largest Coast Guard Base in the U.S. My company will be providing water taxi and freight transport logistics to the villages and many hunting and fishing lodges as well as remote properties around the island.

I would like a business card that isn't status quo, something that stands out, either in feel or appearance. I do like clean minimal designs but it needs to have the necessary contact info on it.

Target Market(s)

remote lodge / property owners, residents of the many villages around Kodiak and any one wanting to enjoy the great outdoors of Kodiak Alaska

Industry/Entity Type

Business

Contact Information for Business Card

I like clean simple designs that aren't cluttered but still provide the necessary information

Colors
0255a3
3277b5
33a4d5
9bcb3c
add136
fbed22
ffc214
f78f20
f37122

Requirements
Must have
• logo and contact info
• Captain Mason Elwick
• www.marrowbyferryline.com
• mason@marrowbyferryline.com

```html
<!DOCTYPE html>
<html lang="en">
<head>
<meta charset="utf-8">
<title>Marrowby Water Taxi and Transport – Business Card</title>
<link rel="stylesheet" href="https://fonts.googleapis.com/css2?family=Mulish:wght@400;600;700&display=swap">
<style>
  :root {
    --page-bg: #dcdfe2;
    --card-bg: #eef2f5;
    --blue-deep: #0255a3;
    --blue-mid: #3277b5;
    --blue-light: #33a4d5;
    --orange: #f37122;
    --text-light: #ffffff;
    --text-soft: #e6f2fa;
  }
  * { box-sizing: border-box; margin: 0; padding: 0; }
  html, body {
    width: 1200px;
    height: 969px;
    overflow: hidden;
    background: var(--page-bg);
    font-family: "Mulish", Arial, sans-serif;
  }
  .card {
    position: absolute;
    left: 100px;
    top: 199px;
    width: 1000px;
    height: 571px;
    border-radius: 22px;
    background: var(--card-bg);
    overflow: hidden;
    box-shadow: 0 10px 30px rgba(0, 0, 0, 0.12);
  }
  .card__artwork {
    position: absolute;
    inset: 0;
    width: 100%;
    height: 100%;
  }
  .card__brand {
    position: absolute;
    left: 636px;
    top: 178px;
    display: flex;
    align-items: center;
    gap: 16px;
    color: var(--blue-deep);
    font-weight: 700;
  }
  .card__brand-dot {
    width: 44px;
    height: 44px;
    border-radius: 50%;
    background: var(--orange);
    flex: none;
  }
  .card__brand-name {
    font-size: 46px;
    line-height: 1;
    letter-spacing: 1px;
    text-transform: uppercase;
  }
  .card__brand-tagline {
    font-size: 22px;
    line-height: 1.2;
    margin-top: 6px;
  }
  .card__person {
    position: absolute;
    left: 38px;
    top: 322px;
    color: var(--text-light);
  }
  .card__name {
    font-size: 30px;
    font-weight: 600;
    letter-spacing: 1px;
    text-transform: uppercase;
  }
  .card__role {
    font-size: 25px;
    font-weight: 400;
    color: var(--text-soft);
    margin-top: 4px;
  }
  .card__contacts {
    position: absolute;
    left: 40px;
    top: 422px;
    list-style: none;
    color: var(--text-light);
    font-size: 22px;
  }
  .card__contact {
    display: flex;
    align-items: center;
    gap: 18px;
    height: 37px;
  }
  .card__icon {
    width: 20px;
    height: 20px;
    flex: none;
    fill: var(--text-light);
  }
</style>
</head>
<body>
  <div class="card">
    <svg class="card__artwork" viewBox="0 0 1000 571" preserveAspectRatio="none"
         role="img" aria-label="Illustration of blue snow-capped mountains with an orange rising sun">
      <defs>
        <linearGradient id="artwork-tone" x1="0" y1="0" x2="1" y2="1">
          <stop offset="0" stop-color="#3a8fcf"/>
          <stop offset="0.6" stop-color="#33a4d5"/>
          <stop offset="1" stop-color="#3277b5"/>
        </linearGradient>
      </defs>
      <polygon points="0,40 520,40 760,571 0,571" fill="url(#artwork-tone)"/>
    </svg>

    <div class="card__brand">
      <span class="card__brand-dot"></span>
      <div>
        <div class="card__brand-name">Marrowby</div>
        <div class="card__brand-tagline">Water Taxi and Transport</div>
      </div>
    </div>

    <div class="card__person">
      <div class="card__name">Mason Elwick</div>
      <div class="card__role">Captain</div>
    </div>

    <ul class="card__contacts">
      <li class="card__contact">
        <svg class="card__icon" viewBox="0 0 24 24" aria-hidden="true"><path d="M6.6 10.8a15.1 15.1 0 0 0 6.6 6.6l2.2-2.2c.3-.3.7-.4 1-.2 1.1.4 2.3.6 3.6.6.6 0 1 .4 1 1V20c0 .6-.4 1-1 1A17 17 0 0 1 3 4c0-.6.4-1 1-1h3.5c.6 0 1 .4 1 1 0 1.3.2 2.5.6 3.6.1.3 0 .7-.2 1z"/></svg>
        <span>555 210 4417</span>
      </li>
      <li class="card__contact">
        <svg class="card__icon" viewBox="0 0 24 24" aria-hidden="true"><path d="M2 5h20v14H2zm2 2v.4l8 5 8-5V7zm0 2.8V17h16V9.8l-8 5z"/></svg>
        <span>mason@marrowbyferryline.com</span>
      </li>
      <li class="card__contact">
        <svg class="card__icon" viewBox="0 0 24 24" aria-hidden="true"><path d="M12 2a10 10 0 1 0 0 20 10 10 0 0 0 0-20zm-1 17.9A8 8 0 0 1 4.2 10l4.8 4.8v1a2 2 0 0 0 2 2zm6.9-2.5a2 2 0 0 0-1.9-1.4h-1v-3a1 1 0 0 0-1-1H8v-2h2a1 1 0 0 0 1-1V7h2a2 2 0 0 0 2-2v-.4a8 8 0 0 1 2.9 12.8z"/></svg>
        <span>www.marrowbyferryline.com</span>
      </li>
    </ul>
  </div>
</body>
</html>
```